Sunset Harbor Living Web Page

We need a web page design that has two intro pages - first being a 'home page', then a link to the second page that has the 'content tabs' and a 'call to action' (see below).

The business helps people that wish to retire to S.E.Asia (Thailand, Malaysia, Indonesia,The Philippines etc) - to enjoy the lifestyle and the remaining years of their lives. What attracts S.E.Asia to many people is the lower cost, the atmoshpere and beauty of the tropics and the vibrancy of the various countries.

People that are wishing to make the most of their retirement and are adventurous at a great bargain compared to the cost of their own countries will be interested.

We help them achieve this - visa, financials (tax, gov't payments etc), introduce them to the right people for property, clubs, retirement facilities, insurance and so forth.

Therefore we are providing an extremely wide ranging service and this site will provide broad but general information only - with a call to action to come and see us for more specific information and how we can help them specifically.

This site will be predominantly for travel and lifestyle, it will be linked with another financial services (financial planning) site later down the track.

The colour scheme is dark green and blue - as per the attached logo design. Photos and background just think lifestyle and S.E.Asia - beaches/mountains/water/recreational activities for retirees.

Target market is mostly those coming up to retirement to those that are already retired. But we also expect to have some interest with younger people that would like to find out more and plan for the future. So a broad age group but I would say mostly 40-70 yrs old.

On the first (Home) page we would like our company name 'Sunset Harbor Living', our logo (which will be on all pages) and a statement such as: “Imagine a retirement where your dreams are brought to life, and you have never felt more alive. Let us show you how”. Then a link to the second page.

We would like an uncluttered site. On the second (contents) page the tabs would be:

- Visa
- Property
- Financials
- Travel
- Insurance & Healthcare
- Medical Tourism
- Cost of living
- Weekly Blogs and articles
- Sunset Harbor Living story

We would also like a call to action on the second page - asking them to leave their contact details if they wish to learn more or sign up to our weekly newsletter/blog.

We are open to suggestions and your imaginations.

Thank you
Malcolm

Font styles to use
Serif
Script

Colors
0255a3
3377b5
00a990
9bcb3c
abd036
33b8a4
85abd2
cadf82
86cfc6

Requirements
Must have
• I have been asked by the web designer to receive a 'Web Font' so that we can 'get off of Zentrofy'. Hope that makes sense.

```html
<!DOCTYPE html>
<html lang="en">
<head>
<meta charset="utf-8">
<title>Sunset Harbor Living</title>
<link href="https://fonts.googleapis.com/css2?family=Cinzel:wght@700&family=Roboto:wght@400;500;700&family=Lato:ital,wght@0,400;0,700;1,400&display=swap" rel="stylesheet">
<style>
:root{
  --ink:#2b2b2b;
  --grey:#6b6b6b;
  --header:#1c1c1c;
  --blue:#1ea0dc;
  --blue-dark:#0a7fc0;
  --green:#12a24a;
  --green-dark:#0c8a3c;
  --light:#f4f4f4;
  --footer:#1a1a1a;
  --white:#ffffff;
  --line:#d9d9d9;
}
*{box-sizing:border-box;margin:0;padding:0}
html,body{width:1200px;height:2711px;overflow:hidden}
body{font-family:"Lato",sans-serif;color:var(--ink);background:var(--white);position:relative}
.abs{position:absolute}

/* header */
.site-header{position:absolute;left:0;top:0;width:1200px;height:100px;background:linear-gradient(#2a2a2a,#111)}
.brand{position:absolute;left:81px;top:22px;display:flex;align-items:center;gap:14px}
.brand-dot{width:52px;height:52px;border-radius:50%;background:var(--green)}
.brand-name{font-family:"Roboto",sans-serif;font-weight:700;font-size:30px;color:var(--white)}
.main-nav{position:absolute;right:80px;top:60px;display:flex;gap:36px}
.main-nav a{font-family:"Roboto",sans-serif;font-weight:500;font-size:15px;color:var(--white);text-decoration:none;position:relative}
.main-nav a.active::after{content:"";position:absolute;left:0;right:0;top:31px;height:5px;background:var(--green)}
.social{display:flex;gap:12px}
.social span{width:28px;height:28px;border:2px solid var(--white);border-radius:50%;display:block}
.header-social{position:absolute;right:80px;top:18px}

/* hero */
.hero{position:absolute;left:0;top:100px;width:1200px;height:583px;background:linear-gradient(180deg,#3fa9a3 0%,#5fbfb6 35%,#9fcfc4 62%,#cdbda0 80%,#b8a486 100%)}
.hero-arrow{position:absolute;top:243px}
.hero-title{position:absolute;left:0;top:278px;width:1200px;text-align:center;font-family:"Cinzel",serif;font-weight:700;font-size:33px;line-height:41px;color:#1f9e3e;text-shadow:0 0 2px #0b3a18,1px 1px 3px #000}
.btn{display:flex;align-items:center;justify-content:space-between;color:var(--white);font-family:"Roboto",sans-serif;font-weight:700;text-decoration:none;border-radius:4px;background:var(--blue)}
.btn .go{display:flex;align-items:center;justify-content:center;background:var(--green);border-radius:50%;border:2px solid var(--white)}
.hero-btn{position:absolute;left:434px;top:446px;width:332px;height:54px;font-size:23px;padding-left:14px;border:2px solid var(--white)}
.hero-btn .go{width:48px;height:48px;margin-right:-2px}

/* welcome */
.welcome{position:absolute;left:0;top:683px;width:1200px;height:343px;background:var(--light);overflow:hidden}
.welcome-mark{position:absolute;left:30px;top:30px;width:260px;height:260px;border-radius:50%;background:#e4ecea}
.section-title{font-family:"Roboto",sans-serif;font-weight:500;text-align:center;font-size:38px}
.divider{position:absolute;left:50%;transform:translateX(-50%);width:540px;height:12px}
.divider::before{content:"";position:absolute;left:0;right:0;top:5px;height:1px;background:currentColor;opacity:.45}
.divider::after{content:"";position:absolute;left:50%;top:0;width:14px;height:12px;margin-left:-7px;border-radius:50%;background:currentColor}
.welcome .section-title{position:absolute;top:50px;width:100%;color:#555}
.welcome .section-title b{color:var(--blue);font-weight:500}
.welcome .divider{top:103px;color:#9aa;width:540px}
.welcome p{position:absolute;left:118px;top:138px;width:964px;text-align:center;font-size:14.5px;line-height:24px;color:#444}
.small-btn{position:absolute;height:36px;font-size:15px;padding-left:12px}
.small-btn .go{width:36px;height:36px}

/* services */
.services{position:absolute;left:0;top:1026px;width:1200px;height:452px;background:var(--blue)}
.services .section-title{position:absolute;top:44px;width:100%;color:var(--white)}
.services .divider{top:94px;color:#0d6f9f;width:420px}
.service-card{position:absolute;top:140px;width:239px;height:159px;border:4px solid var(--white);box-shadow:0 2px 6px rgba(0,0,0,.3)}
.service-label{position:absolute;top:314px;width:239px;text-align:center;font-family:"Roboto",sans-serif;font-weight:500;font-size:20px;color:var(--white)}
.svc-arrow{position:absolute;top:202px}
.view-all{position:absolute;left:492px;top:371px;width:215px;height:38px;background:var(--green);color:var(--white);font-family:"Roboto",sans-serif;font-weight:700;font-size:15px;display:flex;align-items:center;justify-content:center;border-radius:2px}

/* news & testimonials */
.info{position:absolute;left:0;top:1478px;width:1200px;height:452px;background:var(--white)}
.col-title{position:absolute;top:44px;font-family:"Roboto",sans-serif;font-size:36px;color:#777}
.col-title b{color:var(--ink);font-weight:500}
.col-rule{position:absolute;top:108px;height:1px;background:var(--line)}
.pager{position:absolute;top:60px}
.col-split{position:absolute;left:609px;top:44px;width:1px;height:362px;background:var(--line)}
.news-item{position:absolute;left:81px;width:486px}
.news-thumb{position:absolute;left:0;top:0;width:100px;height:100px;border:3px solid var(--white);box-shadow:0 1px 4px rgba(0,0,0,.35)}
.news-body{position:absolute;left:123px;top:0;width:363px}
.news-body h3{font-family:"Roboto",sans-serif;font-weight:500;font-size:15px;color:#222}
.news-body .date{font-style:italic;font-size:11.5px;color:#888;margin-top:6px}
.news-body p{font-size:12px;line-height:18px;color:#555;margin-top:4px}
.news-body .more{font-weight:700;font-size:11px;color:var(--green);margin-top:2px}
.news-sep{position:absolute;left:81px;top:263px;width:486px;height:1px;background:var(--line)}
.avatar{position:absolute;left:650px;top:130px;width:84px;height:84px;border-radius:50%;border:4px solid var(--blue);background:linear-gradient(#cfd8de,#9aa8b2)}
.t-name{position:absolute;left:759px;top:150px;font-family:"Roboto",sans-serif;font-weight:700;font-size:16px;color:#222}
.t-role{position:absolute;left:759px;top:176px;font-size:13px;font-weight:700;color:var(--green)}
.t-quote{position:absolute;left:654px;top:240px;width:466px;font-style:italic;font-size:13px;line-height:27px;color:#444}
.t-quote .q{font-family:"Roboto",sans-serif;font-style:normal;font-weight:700;font-size:28px;line-height:10px;color:#222;vertical-align:-8px}

/* contact */
.contact{position:absolute;left:0;top:1930px;width:1200px;height:480px;background:linear-gradient(180deg,#3a4348 0%,#2f3e45 45%,#24485a 75%,#1d3a48 100%)}
.contact .section-title{position:absolute;top:54px;width:100%;color:var(--white)}
.contact .divider{top:106px;color:#c8cfd2;width:540px}
.field{position:absolute;height:40px;background:var(--white);font-size:12.5px;color:#666;padding:0 12px;display:flex;align-items:center}
.wave{position:absolute;left:0;top:2230px;width:1200px;height:200px}

/* footer */
.site-footer{position:absolute;left:0;top:2400px;width:1200px;height:260px;background:var(--footer)}
.map{position:absolute;left:81px;top:30px;width:262px;height:185px;background:linear-gradient(135deg,#e9e4d6,#cfdcc8 60%,#b9d0e4);border:3px solid #fff}
.foot-about{position:absolute;left:366px;top:30px;width:200px;color:#cfcfcf;font-size:13px;line-height:20px}
.foot-about h4{font-family:"Roboto",sans-serif;font-weight:700;font-size:13px;color:var(--white);margin-bottom:4px}
.contact-line{position:absolute;left:366px;display:flex;gap:10px;align-items:flex-start}
.contact-line .ic{width:22px;height:22px;border:2px solid var(--green);border-radius:50%;display:flex;align-items:center;justify-content:center}
.contact-line small{display:block;font-size:11px;color:#bbb}
.contact-line span{font-size:14px;color:var(--white)}
.newsletter{position:absolute;left:596px;top:62px;width:250px}
.newsletter h4{font-family:"Roboto",sans-serif;font-weight:700;font-size:18px;color:var(--white);display:flex;align-items:center;gap:10px}
.newsletter p{font-size:12px;color:#ddd;margin-top:10px}
.newsletter .email{margin-top:12px;width:240px;height:38px;border:1px solid #777;background:#111;color:#eee;font-size:12px;padding:0 10px;display:flex;align-items:center}
.newsletter .signup{margin-top:12px;width:124px;height:38px;background:var(--green);color:var(--white);font-family:"Roboto",sans-serif;font-weight:700;font-size:15px;display:flex;align-items:center;justify-content:center}
.foot-brand{position:absolute;left:880px;top:70px;width:250px;text-align:center}
.foot-brand .brand-dot{width:90px;height:90px;margin:0 auto 10px}
.foot-brand .brand-name{font-size:28px}
.bottom-bar{position:absolute;left:0;top:2660px;width:1200px;height:51px;background:var(--green)}
.bottom-bar p{position:absolute;left:81px;top:17px;font-size:13px;font-weight:700;color:var(--white)}
.bottom-social{position:absolute;right:80px;top:11px}
</style>
</head>
<body>

<header class="site-header">
  <div class="brand"><span class="brand-dot"></span><span class="brand-name">Sunset Harbor Living</span></div>
  <div class="social header-social"><span></span><span></span><span></span><span></span></div>
  <nav class="main-nav">
    <a class="active" href="#">HOME</a><a href="#">SERVICES</a><a href="#">BLOG &amp; ARTICLES</a><a href="#">OUR STORY</a><a href="#">CONTACT US</a>
  </nav>
</header>

<section class="hero" role="img" aria-label="Photo of a retired couple sitting together on a tropical beach facing turquoise water">
  <svg class="hero-arrow" style="left:40px" width="44" height="74" viewBox="0 0 44 74"><polyline points="40,3 5,37 40,71" fill="none" stroke="#fff" stroke-width="3"/></svg>
  <svg class="hero-arrow" style="right:40px" width="44" height="74" viewBox="0 0 44 74"><polyline points="4,3 39,37 4,71" fill="none" stroke="#fff" stroke-width="3"/></svg>
  <h1 class="hero-title">Imagine A Retirement Where Your Dreams Are<br>Brought To Life,<br>&amp; You Have Never Felt More Alive</h1>
  <a class="btn hero-btn" href="#">Let Us Show You How<span class="go"><svg width="22" height="18" viewBox="0 0 22 18"><polyline points="2,2 9,9 2,16" fill="none" stroke="#fff" stroke-width="2.5"/><polyline points="11,2 18,9 11,16" fill="none" stroke="#fff" stroke-width="2.5"/></svg></span></a>
</section>

<section class="welcome">
  <div class="welcome-mark"></div>
  <h2 class="section-title">Welcome To <b>Sunset Harbor Living</b></h2>
  <div class="divider"></div>
  <p>Lorem ipsum dolor sit amet, consectetuer adipiscing elit, sed diam nonummy nibh euismod tincidunt ut laoreet dolore magna aliquam erat volutpat. Ut wisi enim ad minim veniam, quis nostrud exerci tation ullamcorper suscipit lobortis nisl ut aliquip ex ea commodo consequat. Duis autem vel eum iriure dolor in hendrerit in vulputate velit esse molestie consequat, vel illum dolore eu feugiat nulla facilisis at vero eros et accumsan et iusto odio dignissim qui blandit praesent luptatum zzril delenit augue duis dolore te feugait nulla facilisi.</p>
  <a class="btn small-btn" style="left:526px;top:257px;width:146px" href="#">READ MORE<span class="go"><svg width="18" height="14" viewBox="0 0 18 14"><polyline points="2,2 7,7 2,12" fill="none" stroke="#fff" stroke-width="2"/><polyline points="9,2 14,7 9,12" fill="none" stroke="#fff" stroke-width="2"/></svg></span></a>
</section>

<section class="services">
  <h2 class="section-title">Our Services</h2>
  <div class="divider"></div>
  <svg class="svc-arrow" style="left:36px" width="18" height="30" viewBox="0 0 18 30"><polyline points="15,2 3,15 15,28" fill="none" stroke="#fff" stroke-width="2.5"/></svg>
  <svg class="svc-arrow" style="right:36px" width="18" height="30" viewBox="0 0 18 30"><polyline points="3,2 15,15 3,28" fill="none" stroke="#fff" stroke-width="2.5"/></svg>
  <div class="service-card" style="left:81px;background:linear-gradient(135deg,#c89a6a,#8a5a3a)" role="img" aria-label="Photo of a passport with visa stamps"></div>
  <div class="service-card" style="left:347px;background:linear-gradient(135deg,#8fbf5a,#3f7a2a)" role="img" aria-label="Photo of a hand holding a small model house"></div>
  <div class="service-card" style="left:614px;background:linear-gradient(135deg,#d8e2ee,#6f88a8)" role="img" aria-label="Photo of financial papers, calculator and pen"></div>
  <div class="service-card" style="left:880px;background:linear-gradient(180deg,#6e9cc8,#e6eef5 70%,#c8d2dc)" role="img" aria-label="Photo of a traveller resting on a snowy mountain"></div>
  <div class="service-label" style="left:81px">VISA</div>
  <div class="service-label" style="left:347px">PROPERTY</div>
  <div class="service-label" style="left:614px">FINANCIALS</div>
  <div class="service-label" style="left:880px">TRAVEL</div>
  <div class="view-all">VIEW ALL SERVICE</div>
</section>

<section class="info">
  <h2 class="col-title" style="left:81px">Latest <b>News</b></h2>
  <div class="col-rule" style="left:81px;width:486px"></div>
  <svg class="pager" style="left:528px" width="40" height="24" viewBox="0 0 40 24"><polyline points="12,2 3,12 12,22" fill="none" stroke="#bbb" stroke-width="2"/><polyline points="28,2 37,12 28,22" fill="none" stroke="#333" stroke-width="2"/></svg>

  <article class="news-item" style="top:145px">
    <div class="news-thumb" style="background:linear-gradient(180deg,#5fb4d8,#e6d7b2)" role="img" aria-label="Photo of a palm tree on a white sand beach"></div>
    <div class="news-body">
      <h3>Ut tellus dolor, dapibus smit dollar nomk egemop</h3>
      <p class="date">Posted On 01.01.2015</p>
      <p>Duis autem vel eum iriure dolor in hendrerit in at vero erosacc sa iusto odio dignissim quosli blandit praesent luptatum zzrilni duis</p>
      <p class="more">READ MORE</p>
    </div>
  </article>
  <div class="news-sep"></div>
  <article class="news-item" style="top:291px">
    <div class="news-thumb" style="background:linear-gradient(180deg,#e9c48a,#8a5a32)" role="img" aria-label="Photo of a family walking on a beach at sunset"></div>
    <div class="news-body">
      <h3>Ut tellus dolor, dapibus smit dollar nomk egemop</h3>
      <p class="date">Posted On 01.01.2015</p>
      <p>Duis autem vel eum iriure dolor in hendrerit in at vero erosacc sa iusto odio dignissim quosli blandit praesent luptatum zzrilni duis</p>
      <p class="more">READ MORE</p>
    </div>
  </article>

  <div class="col-split"></div>

  <h2 class="col-title" style="left:652px">Client <b>Testimonials</b></h2>
  <div class="col-rule" style="left:652px;width:468px"></div>
  <svg class="pager" style="left:1080px" width="40" height="24" viewBox="0 0 40 24"><polyline points="12,2 3,12 12,22" fill="none" stroke="#bbb" stroke-width="2"/><polyline points="28,2 37,12 28,22" fill="none" stroke="#333" stroke-width="2"/></svg>
  <div class="avatar" role="img" aria-label="Portrait photo of the client"></div>
  <div class="t-name">MR. QUIS NOSTRUD EXERCI</div>
  <div class="t-role">Business Man</div>
  <p class="t-quote"><span class="q">&ldquo;</span> Utm tellus dolor, dapibus eget, elemen velmki cursus eleifelita arnanokmn auctorbni wisi et urnam. Lorem ipsum dolor sit amet, conse ctetur adipisc ngop elit. Nulla in sollic itudin velit, bibendum velit.Cras vel facilisis ipsum,et venenat risus. Duis autem vel eum iriure dolor in hendrerit in at vero erosacc sa iustoml odio dignissim quosliin sollic itudin <span class="q">&rdquo;</span></p>
</section>

<section class="contact" role="img" aria-label="Background photo of a tropical shoreline with palm leaves at dusk">
  <h2 class="section-title">Get In Touch</h2>
  <div class="divider"></div>
  <div class="field" style="left:210px;top:159px;width:247px">Enter Your Name</div>
  <div class="field" style="left:475px;top:159px;width:250px">Enter Your Email Address</div>
  <div class="field" style="left:743px;top:159px;width:247px">Enter Your Phone Number</div>
  <div class="field" style="left:210px;top:217px;width:247px">Enter Your Location</div>
  <div class="field" style="left:475px;top:217px;width:515px">Enter Your Comments</div>
  <a class="btn small-btn" style="left:535px;top:276px;width:128px" href="#">SUBMIT<span class="go"><svg width="18" height="14" viewBox="0 0 18 14"><polyline points="2,2 7,7 2,12" fill="none" stroke="#fff" stroke-width="2"/><polyline points="9,2 14,7 9,12" fill="none" stroke="#fff" stroke-width="2"/></svg></span></a>
</section>

<svg class="wave" viewBox="0 0 1200 200" preserveAspectRatio="none">
  <path d="M0,150 C300,40 520,210 820,140 C980,100 1100,40 1200,0 L1200,200 L0,200 Z" fill="var(--blue)"/>
  <path d="M0,190 C300,80 520,240 820,172 C980,136 1100,80 1200,44 L1200,200 L0,200 Z" fill="var(--footer)"/>
</svg>

<footer class="site-footer">
  <div class="map" role="img" aria-label="Street map showing the office location"></div>
  <div class="foot-about">
    <h4>SUNSET HARBOR LIVING</h4>
    <p>Duis autem vel eum iriure dolor in hendrerit in at vero</p>
  </div>
  <div class="contact-line" style="top:110px">
    <span class="ic"><svg width="12" height="12" viewBox="0 0 12 12"><path d="M2,1 L4.5,1 L5.5,4 L4,5 C4.8,6.6 5.6,7.4 7,8 L8,6.5 L11,7.5 L11,10 C6,11 1,6 2,1 Z" fill="var(--green)"/></svg></span>
    <div><small>Call Us Today</small><span>(555) 014-2280</span></div>
  </div>
  <div class="contact-line" style="top:168px">
    <span class="ic"><svg width="12" height="10" viewBox="0 0 12 10"><rect x="1" y="1" width="10" height="8" fill="none" stroke="var(--green)" stroke-width="1.4"/><polyline points="1,1 6,5.5 11,1" fill="none" stroke="var(--green)" stroke-width="1.4"/></svg></span>
    <div><small>Write To Us</small><span>hello@sunsetharborliving.com</span></div>
  </div>
  <div class="newsletter">
    <h4><svg width="22" height="16" viewBox="0 0 22 16"><path d="M0,0 L22,8 L0,16 L5,8 Z" fill="var(--green)"/></svg>Newsletter Signup</h4>
    <p>Sign Up To Our Weekly Newsletter/ Blog!</p>
    <div class="email">Enter Your Email Here</div>
    <div class="signup">SIGNUP</div>
  </div>
  <div class="foot-brand">
    <div class="brand-dot"></div>
    <div class="brand-name">Sunset Harbor Living</div>
  </div>
</footer>

<div class="bottom-bar">
  <p>Copyright &copy; 2016 Sunset Harbor Living &nbsp;|&nbsp; All Rights Reserved.</p>
  <div class="social bottom-social"><span></span><span></span><span></span><span></span></div>
</div>

</body>
</html>
```